Business Card - high end, modern health care

Hey designers!

We need a double sided business card for the boutique, cutting edge physical therapy rehabilitation centre in Sydney's Northern Beaches.

With the most qualified physios in the area The Harbourview Motion Clinic does what other physiotherapy practices do not, we take our time with our patients giving them longer appointments, better physios and therefor faster results!

We guarantee that the service people receive at THMC will be unparalleled.

Hence we need a business card to reflect our modern, boutique, high end service. The final design needs to reflect that we are in a class of our own yet with the feel of beachside retreat.

Below I have attached our logo in both blue on white and white on blue. The exact colour is;
and the font that we have used in our logo is Tex Gyre Aventador.

I like the idea of the blue as the main colour as it is more eye catching and our signage onto the main road will be in this blue and in the interest of consistency across marketing the blue needs to be a part of the design. However I would appreciate a few designs onto a wooden background as this is a visual theme within the fitout of the practice.

The design needs to be of standard size (91x55mm).

Target Market(s)

We target people who have an end outcome in mind and those who have had poor experiences with other providers and ensure that everyone gets the care that they deserve with a premium service that is tailored to the individuals circumstances. As a premium service, the target market is highly educated, business and tech savvy with the additional target market of elderly people who have self funded their retirement and see value in paying for the best ongoing rehabilitation to maintain independence.

Industry/Entity Type

Physical Therapy

Contact Information for Business Card

Name, designation( Titled Musculoskeletal Physiotherapist... there will also be those in the company that have multiple designations ie 5 or 6 words long), phone number, email, facebook, instagram, address

Font styles to use
Sans Serif

Colors

Designer to choose colors to be used in the design.

Requirements
Must have
• Front - The logo as large as possible, blue or wooden theme, and all of the important details.
• Back - A blank space/lines on which to write appointment times (no "Appointment, date, time" etc.)
Nice to have
• facebook url
• logos for facebook and instagram
• Mini logos for the phone and email?

```html
<!DOCTYPE html>
<html lang="en">
<head>
<meta charset="utf-8">
<title>The Harbourview Motion Clinic – Business Card</title>
<link href="https://fonts.googleapis.com/css2?family=Lato:wght@300;400;700;900&display=swap" rel="stylesheet">
<style>
  :root {
    --brand-blue: #0a56a8;
    --paper: #f1f1f1;
    --paper-mark: #e3e3e3;
    --ink-light: #ffffff;
    --stage: #3a3a3a;
    --rule: rgba(255,255,255,0.55);
  }
  * { margin: 0; padding: 0; box-sizing: border-box; }
  html, body { width: 1200px; height: 782px; overflow: hidden; }
  body {
    background: var(--stage);
    font-family: "Lato", sans-serif;
    position: relative;
  }
  .card {
    position: absolute;
    width: 540px;
    height: 326px;
    overflow: hidden;
    box-shadow: 0 10px 24px rgba(0,0,0,0.35);
  }

  /* ---------- Front (blue) ---------- */
  .card-front {
    left: 40px;
    top: 228px;
    background: var(--brand-blue);
    color: var(--ink-light);
  }
  .front-brand {
    position: absolute;
    left: 200px;
    top: 40px;
    display: flex;
    align-items: center;
    gap: 14px;
  }
  .brand-dot {
    width: 56px; height: 56px;
    border-radius: 50%;
    background: var(--ink-light);
    flex: none;
  }
  .brand-name {
    font-weight: 900;
    font-size: 27px;
    line-height: 1.05;
    letter-spacing: 0.5px;
    text-transform: uppercase;
  }
  .brand-name .line-two {
    display: block;
    letter-spacing: 5px;
    font-size: 20px;
  }
  .person {
    position: absolute;
    left: 34px;
    top: 150px;
    width: 472px;
  }
  .person-name {
    font-weight: 700;
    font-size: 21px;
    letter-spacing: 0.3px;
    text-transform: uppercase;
  }
  .person-title {
    font-weight: 400;
    font-size: 13px;
    margin-top: 2px;
  }
  .person-rule {
    height: 1px;
    background: var(--rule);
    margin-top: 10px;
  }
  .contact {
    position: absolute;
    right: 34px;
    bottom: 30px;
    list-style: none;
    text-align: right;
    font-size: 17px;
    font-weight: 400;
  }
  .contact li {
    display: flex;
    justify-content: flex-end;
    align-items: center;
    gap: 10px;
    margin-top: 8px;
  }
  .contact-icon {
    width: 20px; height: 20px;
    flex: none;
  }

  /* ---------- Back (white) ---------- */
  .card-back {
    left: 620px;
    top: 228px;
    background: var(--paper);
  }
  .back-mark {
    position: absolute;
    left: 190px;
    top: 40px;
    width: 250px;
    height: 250px;
    border-radius: 50%;
    background: var(--paper-mark);
  }
  .back-band {
    position: absolute;
    left: 0;
    top: 196px;
    width: 330px;
    height: 100px;
  }
  .social {
    position: absolute;
    left: 18px;
    top: 205px;
    display: flex;
    align-items: center;
    gap: 7px;
    color: var(--ink-light);
    font-size: 14px;
    font-weight: 400;
  }
  .social-dot {
    width: 20px; height: 20px;
    border-radius: 50%;
    background: var(--ink-light);
  }
  .social-handle { margin-left: 6px; }
  .back-brand {
    position: absolute;
    left: 300px;
    top: 240px;
    display: flex;
    align-items: center;
    gap: 8px;
    color: var(--brand-blue);
  }
  .back-brand .brand-dot {
    width: 34px; height: 34px;
    background: var(--brand-blue);
  }
  .back-brand .brand-name { font-size: 16px; }
  .back-brand .brand-name .line-two { font-size: 12px; letter-spacing: 3px; }
</style>
</head>
<body>

  <section class="card card-front" aria-label="Business card front">
    <div class="front-brand">
      <span class="brand-dot"></span>
      <p class="brand-name">The Harbourview<span class="line-two">Motion Clinic</span></p>
    </div>

    <div class="person">
      <p class="person-name">Daniel Hartley</p>
      <p class="person-title">Managing Director</p>
      <div class="person-rule"></div>
    </div>

    <ul class="contact">
      <li>444 555 7720
        <svg class="contact-icon" viewBox="0 0 20 20" aria-hidden="true">
          <circle cx="10" cy="10" r="9" fill="none" stroke="#fff" stroke-width="1.6"/>
          <path d="M7 5.5 l1.6 0 l0.8 2.4 l-1.2 1 a6 6 0 0 0 2.9 2.9 l1 -1.2 l2.4 0.8 l0 1.6 a1 1 0 0 1 -1 1 A8 8 0 0 1 6 6.5 a1 1 0 0 1 1 -1z" fill="#fff"/>
        </svg>
      </li>
      <li>info@harbourviewmotion.com
        <svg class="contact-icon" viewBox="0 0 20 20" aria-hidden="true">
          <circle cx="10" cy="10" r="9" fill="none" stroke="#fff" stroke-width="1.6"/>
          <rect x="5.5" y="6.5" width="9" height="7" rx="0.8" fill="#fff"/>
          <path d="M5.8 7 L10 10.5 L14.2 7" fill="none" stroke="#0a56a8" stroke-width="1.1"/>
        </svg>
      </li>
    </ul>
  </section>

  <section class="card card-back" aria-label="Business card back">
    <div class="back-mark" role="img" aria-label="Faint brand circle"></div>

    <svg class="back-band" viewBox="0 0 330 100" aria-hidden="true">
      <path d="M0 0 H268 A40 40 0 0 0 268 80 V100 H0 Z" fill="#0a56a8"/>
    </svg>

    <div class="social">
      <span class="social-dot"></span>
      <span class="social-dot"></span>
      <span class="social-handle">harbourviewmotionclinic</span>
    </div>

    <div class="back-brand">
      <span class="brand-dot"></span>
      <p class="brand-name">The Harbourview<span class="line-two">Motion Clinic</span></p>
    </div>
  </section>

</body>
</html>
```